Quillbrookes websites redesign

Www.quill-brookes.com needs to be redesigned along with updations. The incremental material will be provided for the updations. We are looking for complete redesign of the pages with the new content. The complete write up will be provided soon

Target Market(s)

Global

Coding

Coded - Design and coding required

Number of Pages Required

5+ page

Requirements
Must have
• A clean and slick design for the Consulting.
Should not have
• Too many pictures which reduces the speed of the site

```html
<!DOCTYPE html>
<html lang="en">
<head>
<meta charset="utf-8">
<title>Quillbrookes – Contact Us</title>
<link href="https://fonts.googleapis.com/css2?family=Arimo:wght@400;700&family=Raleway:wght@300;400;500&display=swap" rel="stylesheet">
<style>
:root{
  --accent:#38a7cd;
  --ink:#333333;
  --muted:#8a8a8a;
  --line:#e3e3e3;
  --footer:#1b1b1b;
  --footer-text:#a9a9a9;
  --white:#ffffff;
}
*{box-sizing:border-box;margin:0;padding:0}
html,body{width:1200px;height:1200px;overflow:hidden;background:var(--white)}
body{position:relative;font-family:"Arimo",Arial,sans-serif;color:var(--ink)}
.abs{position:absolute}
.site-header{position:absolute;left:0;top:0;width:1200px;height:74px;border-bottom:1px solid var(--line)}
.brand{position:absolute;left:226px;top:18px;display:flex;align-items:center;gap:9px;height:40px}
.brand-dot{width:34px;height:34px;border-radius:50%;background:var(--accent)}
.brand-name{font-size:23px;color:#2d3d55;white-space:nowrap}
.main-nav a{position:absolute;top:32px;font-size:12px;color:#555;text-decoration:none;white-space:nowrap}
.main-nav .active{color:var(--accent)}
.nav-underline{position:absolute;left:954px;top:71px;width:56px;height:3px;background:var(--accent)}
.map{position:absolute;left:226px;top:123px;width:783px;height:238px;background:linear-gradient(100deg,#f0ece5,#e9e5dd 60%,#eeeae3)}
.map-card{position:absolute;left:278px;top:123px;width:230px;height:184px}
.map-card-text{position:absolute;left:300px;top:156px;width:200px;color:var(--white);font-size:10px;line-height:17px}
.map-card-text strong{display:block;font-size:11.5px;margin-bottom:16px}
.page-title{position:absolute;left:226px;top:410px;font-family:"Raleway",sans-serif;font-weight:300;font-size:26px;color:#444}
.page-intro{position:absolute;left:227px;top:451px;font-size:10.4px;color:#444}
.field{position:absolute;left:226px;width:356px;border:1px solid #dcdcdc;font-size:10.8px;color:#999;padding:12px 16px}
.send-btn{position:absolute;left:226px;top:763px;width:356px;height:38px;background:var(--accent);color:var(--white);font-family:"Raleway",sans-serif;font-weight:500;font-size:11px;letter-spacing:1.5px;display:flex;align-items:center;justify-content:center}
.info{position:absolute;left:650px;font-size:11px;line-height:17.2px;color:#333}
.info-label{font-family:"Raleway",sans-serif;font-weight:500;font-size:10.5px;letter-spacing:1.4px;color:var(--muted);margin-bottom:13px}
.site-footer{position:absolute;left:0;top:882px;width:1200px;height:318px;background:var(--footer);color:var(--footer-text)}
.footer-brand{position:absolute;left:226px;top:54px;display:flex;align-items:center;gap:7px}
.footer-brand .brand-dot{width:27px;height:27px;background:#8d8d8d}
.footer-brand span{font-size:19px;color:#b8b8b8}
.footer-address{position:absolute;left:229px;top:104px;font-size:10.3px;line-height:17.2px}
.footer-contact{position:absolute;left:229px;top:188px;font-size:10.3px;line-height:17.5px}
.footer-contact b{color:var(--accent);font-size:11.5px}
.footer-contact u{color:var(--accent)}
.footer-heading{position:absolute;top:60px;font-family:"Raleway",sans-serif;font-weight:500;font-size:12px;color:var(--white)}
.footer-heading::after{content:"";position:absolute;left:0;top:24px;width:26px;height:1px;background:#cfcfcf}
.footer-note{position:absolute;left:480px;top:104px;font-size:10.3px}
.subscribe{position:absolute;left:479px;top:130px;width:179px;height:32px;border:1px solid #6a6a6a;font-size:10.3px;color:#ccc;padding:9px 12px}
.footer-links{position:absolute;left:733px;top:102px;list-style:none;font-size:10.3px;line-height:21.4px}
.footer-links li::before{content:"»";color:#777;margin-right:7px;font-size:9px}
.footer-links .active{color:var(--accent);text-decoration:underline}
.footer-rule{position:absolute;left:0;top:268px;width:1200px;height:1px;background:#333}
.copyright{position:absolute;left:227px;top:287px;font-size:10.3px;color:#999}
</style>
</head>
<body>
<header class="site-header">
  <div class="brand"><span class="brand-dot"></span><span class="brand-name">Quillbrookes</span></div>
  <nav class="main-nav">
    <a style="left:568px">Home</a>
    <a style="left:631px">Founder</a>
    <a style="left:698px">Consultancy</a>
    <a style="left:787px">Platform</a>
    <a style="left:856px">Case Studies</a>
    <a class="active" style="left:954px">Contact Us</a>
  </nav>
  <div class="nav-underline"></div>
</header>

<div class="map" role="img" aria-label="Street map showing the office location"></div>
<svg class="map-card" viewBox="0 0 230 184" aria-hidden="true"><polygon points="0,0 230,0 230,184 115,155 0,182" fill="#38a7cd"/></svg>
<div class="map-card-text">
  <strong>Quillbrookes Consultancy Ltd</strong>
  Suite 08, 9th Floor, Harbourline Tower, 27 Lantern Quay Road, Kowloon<br>Hong Kong
</div>

<h1 class="page-title">Contact Us</h1>
<p class="page-intro">Please use the contact form below to send us any information we may need.</p>

<form>
  <div class="field" style="top:508px;height:38px">Name*</div>
  <div class="field" style="top:553px;height:38px">Email Address*</div>
  <div class="field" style="top:598px;height:39px">Phone</div>
  <div class="field" style="top:644px;height:96px">Message</div>
  <div class="send-btn">SEND MESSAGE</div>
</form>

<section class="info" style="top:502px">
  <div class="info-label">ADDRESS</div>
  <b>Quillbrookes Consultancy Ltd</b><br>
  Suite 08, 9th Floor, Harbourline Tower,<br>27 Lantern Quay Road, Kowloon<br>Hong Kong
</section>
<section class="info" style="top:638px">
  <div class="info-label" style="margin-bottom:9px">TELEPHONES</div>
  +852-25550187 (landline)<br>+852-3555 0142 (fax)
</section>
<section class="info" style="top:746px">
  <div class="info-label" style="margin-bottom:9px">EMAIL</div>
  query@quill-brookes.com<br>www.quill-brookes.com
</section>

<footer class="site-footer">
  <div class="footer-brand"><span class="brand-dot"></span><span>Quillbrookes</span></div>
  <p class="footer-address">Quillbrookes Consultancy Ltd<br>Suite 08, 9th Floor, Harbourline Tower,<br>27 Lantern Quay Road, Kowloon<br>Hong Kong</p>
  <p class="footer-contact">T: <b>852-255 50187</b><br>E: <u>query@quill-brookes.com</u></p>

  <div class="footer-heading" style="left:479px">GET IN TOUCH!</div>
  <p class="footer-note">Simply Drop Your Mail Here</p>
  <div class="subscribe">Your Email Here
    <svg class="abs" style="right:8px;top:10px" width="15" height="11" viewBox="0 0 15 11" aria-hidden="true"><rect x="0.5" y="0.5" width="14" height="10" fill="none" stroke="#38a7cd"/><polyline points="0.5,0.5 7.5,6 14.5,0.5" fill="none" stroke="#38a7cd"/></svg>
  </div>

  <div class="footer-heading" style="left:732px">SITE LINKS</div>
  <ul class="footer-links">
    <li>Home</li><li>Founder</li><li>Consultancy</li><li>Platform</li><li>Case Studies</li><li><span class="active">Contact Us</span></li>
  </ul>

  <div class="footer-heading" style="left:897px">SOCIAL LINKS</div>
  <svg class="abs" style="left:897px;top:104px" width="114" height="28" viewBox="0 0 114 28" role="img" aria-label="Social network links">
    <circle cx="13" cy="14" r="12" fill="none" stroke="#38a7cd" stroke-width="1.6"/>
    <circle cx="42" cy="14" r="12" fill="none" stroke="#b5b5b5" stroke-width="1.6"/>
    <circle cx="71" cy="14" r="12" fill="none" stroke="#b5b5b5" stroke-width="1.6"/>
    <circle cx="100" cy="14" r="12" fill="none" stroke="#b5b5b5" stroke-width="1.6"/>
  </svg>

  <div class="footer-rule"></div>
  <p class="copyright">© 2016. Quillbrookes Consultancy Limited</p>
</footer>
</body>
</html>
```